Business Cards Design for the electrical wholesaler: clean bold dynamic :)

We need a business card design that would follow our latest brand guidelines. As an electrical wholesaler we want to bring a fresh look and feel into the industry. The design should be clean bold and dynamic. It should come alive with the renewed energy of our green colour. Our grey colour should keep things balanced and complement the notion of maturity and responsibility. We employ Lato as a corporate font however are not bound by this font and we’re open to interpretation here.

Target Market(s)

Electrical contractors

Industry/Entity Type

Business

Contact Information for Business Card

Logo
Name & Surname: Halyna Dorosh
Job Title: Director of Marketing
Email: halya.dorosh@quillmail.example
Cell phone: XXX.XXX.XXXX
Address: 20517 - 87 Ave. Edmonton, AB, Canada. T6K 4N8
Business Phone: 780.555.0184
Website: www.brovix.example

Font styles to use
Other font styles liked:
• Lato

Requirements
Must have
• Logo & website
Nice to have
• Brand elements - some of them you may find in the attached Brand Guidelines (e.g. three lines on the background signifying "W")

```html
<!DOCTYPE html>
<html lang="en">
<head>
<meta charset="utf-8">
<title>Brovix business card</title>
<link rel="stylesheet" href="https://fonts.googleapis.com/css2?family=Lato:wght@400;700;900&display=swap">
<style>
  :root {
    --backdrop: #2a2a2b;
    --brand-green: #8bbf3c;
    --brand-grey: #4d4d4f;
    --card-white: #f3f3f2;
    --text-white: #ffffff;
    --text-soft: #e2e2e2;
  }
  * { margin: 0; padding: 0; box-sizing: border-box; }
  html, body {
    width: 1200px; height: 960px; overflow: hidden;
    background: var(--backdrop);
    font-family: "Lato", Arial, sans-serif;
  }
  .canvas { position: relative; width: 1200px; height: 960px; }
  .card {
    position: absolute; width: 600px; height: 342px;
    border-radius: 18px; overflow: hidden;
  }
  .card-front { left: 314px; top: 113px; background: var(--card-white); }
  .card-back { left: 311px; top: 472px; background: var(--brand-grey); }
  .front-band { position: absolute; inset: 0; }
  .contact {
    position: absolute; left: 50px; top: 72px; color: var(--text-white);
  }
  .contact-name { font-weight: 700; font-size: 21px; letter-spacing: 0.2px; line-height: 1.15; }
  .contact-title { font-size: 15px; line-height: 1.2; margin-bottom: 12px; }
  .contact-address { font-size: 14.5px; line-height: 1.25; margin-bottom: 10px; }
  .contact-list { list-style: none; font-size: 14.5px; line-height: 19px; }
  .contact-list li { display: flex; align-items: center; gap: 8px; }
  .contact-list svg { width: 14px; height: 14px; flex: none; fill: var(--text-white); }
  .front-brand {
    position: absolute; left: 362px; top: 150px; width: 180px;
    text-align: center; color: var(--brand-grey);
  }
  .front-brand-row { display: flex; align-items: center; justify-content: center; gap: 8px; }
  .brand-dot { width: 14px; height: 14px; border-radius: 50%; background: var(--brand-green); }
  .front-brand-name { font-size: 50px; font-weight: 400; line-height: 1; }
  .front-brand-tag { font-size: 10.5px; font-weight: 700; letter-spacing: 1.2px; margin-top: 6px; }
  .back-brand {
    position: absolute; left: 0; right: 0; top: 100px;
    display: flex; justify-content: center; align-items: center; gap: 14px;
  }
  .back-brand-name { font-size: 84px; font-weight: 900; color: var(--brand-green); line-height: 1; }
  .back-brand .brand-dot { width: 22px; height: 22px; }
  .back-web {
    position: absolute; left: 0; right: 0; top: 290px; text-align: center;
    font-size: 13px; letter-spacing: 3.2px; color: var(--text-soft);
  }
</style>
</head>
<body>
<main class="canvas">
  <section class="card card-front">
    <svg class="front-band" viewBox="0 0 600 342" aria-hidden="true">
      <path d="M0 0 H170 C210 0 228 30 238 80 C262 210 300 300 385 342 H0 Z" fill="var(--brand-green)"/>
    </svg>
    <div class="contact">
      <p class="contact-name">HALYNA DOROSH</p>
      <p class="contact-title">CEO/FOUNDER</p>
      <p class="contact-address">20517 - 87 Ave. Edmonton, AB,<br>Canada. T6K 4N8</p>
      <ul class="contact-list">
        <li><svg viewBox="0 0 16 16"><path d="M3.5 1 6 1.5 7 5 5.4 6.3a9 9 0 0 0 4.3 4.3L11 9l3.5 1 .5 2.5c0 1-1 2-2 2C6.5 14.5 1.5 9.5 1.5 3c0-1 1-2 2-2z"/></svg>780.555.0184</li>
        <li><svg viewBox="0 0 16 16"><path d="M4.5 0h7a1 1 0 0 1 1 1v14a1 1 0 0 1-1 1h-7a1 1 0 0 1-1-1V1a1 1 0 0 1 1-1zm.5 2v10h6V2zm3 11a1 1 0 1 0 0 2 1 1 0 0 0 0-2z"/></svg>780.555.0147</li>
        <li><svg viewBox="0 0 16 16"><path d="M4 1h8v4H4zM1 6h14v6h-2.5v3h-9v-3H1zm4.5 4v3.5h5V10z"/></svg>780.555.0129</li>
        <li><svg viewBox="0 0 16 16"><path d="M1 3h14v1.2L8 9 1 4.2zm0 2.6 7 4.8 7-4.8V13H1z"/></svg>halya.dorosh@quillmail.example</li>
        <li><svg viewBox="0 0 16 16"><path d="M8 1a7 7 0 1 0 0 14A7 7 0 0 0 8 1zm-1 2.5 1.5 1.5-1 2 2 1.5 1.5-.5.5 2.5-2 2.5-1-2-2-1 .5-2.5-2.5-1L4 4.5z"/></svg>www.brovix.example</li>
      </ul>
    </div>
    <div class="front-brand">
      <div class="front-brand-row">
        <span class="brand-dot"></span>
        <span class="front-brand-name">Brovix</span>
      </div>
      <p class="front-brand-tag">ELECTRICAL WHOLESALERS</p>
    </div>
  </section>

  <section class="card card-back">
    <div class="back-brand">
      <span class="brand-dot"></span>
      <span class="back-brand-name">Brovix</span>
    </div>
    <p class="back-web">www.brovix.example</p>
  </section>
</main>
</body>
</html>
```